Vodka Bottle Label - Luma Vodka

I need a bottle label for a vodka I'd like to make called Luma Vodka.
I would like a label that looks elegant and fresh. I would like some mountains and colours to be red and white. Open to other colours being added but not too colourful. "Luma" means fresh, dawn in polish, i would like if mountains or something extra was added to the label too. I would like the Luma Vodka name not to be too small.
The vodka is made in australia and is 37%.

I would love to have a little bit of gold colour in the label!

I will provide the back label words when completing my decision.

i'd like to make it more simple and less european looking. More australian.

I saw a bottle like this and i did like the concept.

https://www.tallgumcellars.com.au/spirits/qrnt-vodka-range?srsltid=ZtqWXkelmaHuP31-ra-m7s92xudhfew_pT8eWnGBbRTxLsb3hTyQsdGaqYt

Target Market(s)

Vodka Drinkers

Industry/Entity Type

Alcohol

Colors
EB3D1F
EC4F4E
F09395
F8D3D4
FCEDEE

Requirements
Must have
• red and white colours incorporated, mountains or freshness on it.
Nice to have
• Fresh and clean look. Classy

```html
<!DOCTYPE html>
<html lang="en">
<head>
<meta charset="utf-8">
<title>Luma Vodka – Label</title>
<link rel="stylesheet" href="https://fonts.googleapis.com/css2?family=Josefin+Sans:wght@300;400;600&family=Montserrat:wght@600&display=swap">
<style>
  :root {
    --paper: #ffffff;
    --ink-navy: #1f3566;
    --ink-blue: #2a56b4;
    --pill-blue: #2350b6;
    --mark-coral: #e5534f;
    --wordmark-dark: #1c1c1e;
    --sky-light: #3d95d8;
    --ridge-mid: #2a5fb8;
    --forest-deep: #1c2a78;
    --white: #ffffff;
  }
  html, body {
    margin: 0;
    padding: 0;
    width: 1200px;
    height: 2199px;
    overflow: hidden;
    background: var(--paper);
  }
  .canvas {
    position: relative;
    width: 1200px;
    height: 2199px;
    font-family: "Josefin Sans", sans-serif;
  }
  .brand-dot {
    position: absolute;
    left: 580px;
    top: 716px;
    width: 20px;
    height: 20px;
    border-radius: 50%;
    background: var(--mark-coral);
  }
  .tier {
    position: absolute;
    left: 0;
    width: 1175px;
    top: 766px;
    text-align: center;
    font-weight: 600;
    font-size: 15px;
    letter-spacing: 6px;
    color: var(--ink-navy);
  }
  .landscape {
    position: absolute;
    left: 372px;
    top: 862px;
    width: 428px;
    height: 330px;
    border-radius: 46% 54% 40% 48% / 55% 50% 42% 40%;
    background: linear-gradient(180deg, var(--sky-light) 0%, var(--ridge-mid) 45%, var(--forest-deep) 100%);
  }
  .label-name {
    position: absolute;
    left: 0;
    width: 1175px;
    text-align: center;
    color: var(--white);
  }
  .label-name .word {
    position: absolute;
    left: 0;
    width: 100%;
    top: 972px;
    font-weight: 300;
    font-size: 128px;
    line-height: 1;
    letter-spacing: 6px;
  }
  .label-name .kind {
    position: absolute;
    left: 0;
    width: 100%;
    top: 1104px;
    font-weight: 400;
    font-size: 34px;
    letter-spacing: 7px;
  }
  .origin {
    position: absolute;
    left: 0;
    width: 1180px;
    top: 1310px;
    text-align: center;
    font-weight: 400;
    font-size: 26px;
    letter-spacing: 8px;
    color: var(--ink-blue);
  }
  .strength {
    position: absolute;
    left: 492px;
    top: 1367px;
    width: 197px;
    height: 41px;
    border-radius: 21px;
    background: var(--pill-blue);
    color: var(--white);
    font-family: "Montserrat", sans-serif;
    font-weight: 600;
    font-size: 18px;
    line-height: 42px;
    text-align: center;
  }
  .signature-mark {
    position: absolute;
    left: 0;
    width: 1190px;
    text-align: center;
    color: var(--wordmark-dark);
  }
  .signature-mark .word {
    position: absolute;
    left: 0;
    width: 100%;
    top: 1866px;
    font-weight: 300;
    font-size: 92px;
    line-height: 1;
    letter-spacing: 6px;
  }
  .signature-mark .kind {
    position: absolute;
    left: 0;
    width: 100%;
    top: 1956px;
    font-weight: 300;
    font-size: 32px;
    letter-spacing: 9px;
  }
</style>
</head>
<body>
  <main class="canvas">
    <div class="brand-dot"></div>
    <p class="tier" style="margin:0">ULTRA PREMIUM</p>

    <div class="landscape" role="img" aria-label="Watercolour mountain range with a pine forest in blue tones"></div>

    <div class="label-name">
      <span class="word">LUMA</span>
      <span class="kind">VODKA</span>
    </div>

    <p class="origin" style="margin:0">AUSTRALIA</p>
    <div class="strength">37% ALC/ 70 CL</div>

    <div class="signature-mark">
      <span class="word">LUMA</span>
      <span class="kind">VODKA</span>
    </div>
  </main>
</body>
</html>
```